Yacht, Boats, Watersports company needs a redesign of business card

Hello Designers!
We are a Boat dealership company that sells fun in the water, we sell boats, Yachts, Kayaks and also yacht WaterSport toys. We are looking to redesign our business cards in to something a little bit more sophisticated. in a way that we can make better use of our company colors. I'm attaching a zipped file containing the company 3 sets of company logo which one is an horizontal another one is a vertical and also a chromed 3d logo. Also is included two set of business cards that we use and also some designs that i think it's interesting. We use PMS 2026c Orange and PMS 7687C Blue. I would like to see at least two different options with the orange as accent and also using blue as an accent color. It's really important for the business cards to have a font option and size that is legible to most people. Our current website is wwww.coralpennant.com. Please visit if you want to have a better feeling of the Boat dealership
You can send Single sided or double side options. We are now using single sided but we may be open for a double side option if we really like the design.
Target Market(s)
Marine, boat sales, yacht sales, water toys sales/
Contact Information for Business Card
Name: Dale Whitcombe
Address: 212 North Fenwick Lane,
Harbor Point, FL 33817
Phone: 954-731-8842
Fax: 954:731-8843
Cell: 954-382-1490
Email: dw@coralpennant.com
Website: coralpennant.com
Requirements
Must have
- the current information of the business card provided.
logo
use the PMS Colors
Nice to have
- a touch of elegance and sophistication but simple
Should not have
- should not have any typography that is hard to read, the card should be simple but yet sophisticated.

```html
<!DOCTYPE html>
<html lang="en">
<head>
<meta charset="utf-8">
<title>Coral Pennant – Business Card</title>
<link href="https://fonts.googleapis.com/css2?family=Poppins:wght@400;500;600&display=swap" rel="stylesheet">
<style>
  :root {
    --brand-blue: #2a6cb3;
    --brand-blue-deep: #1a569c;
    --brand-blue-light: #3c89cb;
    --brand-orange: #f08a24;
    --text-grey: #454545;
    --rule-grey: #8a8a8a;
    --faint-ring: #e9eff7;
    --page: #e4e4e4;
    --card-white: #ffffff;
  }
  html, body {
    margin: 0;
    width: 1200px;
    height: 1200px;
    overflow: hidden;
    background: var(--page);
  }
  .sheet {
    position: relative;
    width: 1200px;
    height: 1200px;
    font-family: "Poppins", sans-serif;
  }
  .card {
    position: absolute;
    left: 120px;
    width: 960px;
    height: 548px;
    display: block;
  }
  .card--front { top: 24px; }
  .card--back { top: 628px; }
  .brand-name { font-weight: 600; letter-spacing: 0.5px; }
  .person-name { font-weight: 600; font-size: 24px; fill: var(--brand-blue); letter-spacing: 0.3px; }
  .contact-line { font-size: 18px; fill: var(--text-grey); }
  .address-line { font-size: 18px; fill: var(--text-grey); }
  .website { font-size: 18px; fill: var(--card-white); letter-spacing: 1.5px; }
</style>
</head>
<body>
<main class="sheet">

  <svg class="card card--front" viewBox="0 0 800 457" aria-label="Business card front">
    <defs>
      <clipPath id="front-shape"><rect width="800" height="457" rx="20"/></clipPath>
    </defs>
    <g clip-path="url(#front-shape)">
      <rect class="card-face" width="800" height="457" fill="var(--card-white)"/>
      <circle class="faint-ring" cx="170" cy="215" r="195" fill="none" stroke="var(--faint-ring)" stroke-width="28"/>

      <g class="brand-block">
        <circle cx="594" cy="88" r="40" fill="var(--brand-orange)"/>
        <text class="brand-name" x="594" y="180" text-anchor="middle" font-size="27" fill="var(--brand-blue)">CORAL PENNANT</text>
      </g>

      <text class="person-name" x="44" y="285">DALE WHITCOMBE</text>
      <line class="divider" x1="44" y1="302" x2="754" y2="302" stroke="var(--rule-grey)" stroke-width="1"/>

      <g class="contact-list">
        <path d="M47 323 c1-2 3-3 4-2 l2 3 c1 1 0 2-1 3 c1 2 2 3 4 4 c1-1 2-2 3-1 l3 2 c1 1 0 3-2 4 c-6 1-14-7-13-13z" fill="var(--brand-blue)"/>
        <text class="contact-line" x="70" y="336">954-731-8842</text>
        <rect x="48" y="344" width="10" height="15" rx="2" fill="none" stroke="var(--brand-blue)" stroke-width="2"/>
        <text class="contact-line" x="70" y="359">954-382-1490</text>
        <rect x="49" y="367" width="8" height="5" fill="var(--brand-blue)"/>
        <rect x="46" y="372" width="14" height="8" rx="1" fill="var(--brand-blue)"/>
        <text class="contact-line" x="70" y="381">954:731-8843</text>
        <rect x="46" y="394" width="14" height="10" fill="var(--brand-blue)"/>
        <path d="M46 394 l7 5 l7-5" fill="none" stroke="var(--card-white)" stroke-width="1.2"/>
        <text class="contact-line" x="70" y="404">dw@coralpennant.com</text>
      </g>

      <g class="address-block" text-anchor="end">
        <text class="address-line" x="754" y="335">Coral Pennant Marine Center</text>
        <text class="address-line" x="754" y="357">212 North Fenwick Lane</text>
        <text class="address-line" x="754" y="380">Harbor Point, FL 33817</text>
      </g>

      <path class="accent-orange" d="M0 436 L452 436 C448 440 445 443 440 443 L0 443 Z" fill="var(--brand-orange)"/>
      <path class="accent-blue" d="M0 443 L440 443 C455 443 460 430 470 418 C478 410 484 408 495 408 L800 408 L800 457 L0 457 Z" fill="var(--brand-blue)"/>
      <text class="website" x="776" y="437" text-anchor="end">www.coralpennant.com</text>
    </g>
  </svg>

  <svg class="card card--back" viewBox="0 0 800 457" aria-label="Business card back">
    <defs>
      <linearGradient id="back-gradient" x1="1" y1="0" x2="0" y2="1">
        <stop offset="0" stop-color="var(--brand-blue-light)"/>
        <stop offset="1" stop-color="var(--brand-blue-deep)"/>
      </linearGradient>
    </defs>
    <rect class="card-face" width="800" height="457" rx="20" fill="url(#back-gradient)"/>
    <g class="brand-block">
      <circle cx="396" cy="173" r="48" fill="var(--brand-orange)"/>
      <text class="brand-name" x="400" y="298" text-anchor="middle" font-size="36" fill="var(--card-white)">CORAL PENNANT</text>
    </g>
  </svg>

</main>
</body>
</html>
```